International Chino Pant Manufacturer

We need modern packaging design for men's chino. All kinds of packaging designs are welcome.

The pant is folded and packaged in a poly bag. We require a label design for the brand name Tarvo. The main label will be attached by a string on the belt loop. the size of that label will 15cm in length and 5cm wide. This is the first label the customer see's when he picks up the garment. Therefore, we require an eye catching design for that. If required it could have certain information about the chino pant on the main label such as Comfort fit, Wrinkle-resistant, machine washable, luxury fabric. But, if you feel that adding the above information spoils the design of the label then it is not a must to include the above information. On the back of the label we like to include the information that this pant was manufactured in an Brena Summit certified green plant and hence the damage to the environment because of the plant is nill.

The second label label is attached on to the waist band and the purpose of that label is to include the size of the pant such 32x32. The size of that label is 8cm in length and 4cm in width. There is no design on the back on this label it has to be blank.

Industry/Entity Type

Manufacturer

```html
<!DOCTYPE html>
<html lang="en">
<head>
<meta charset="utf-8">
<title>Tarvo Chino Labels</title>
<link href="https://fonts.googleapis.com/css2?family=Black+Ops+One&family=Arimo:wght@700&display=swap" rel="stylesheet">
<style>
  :root {
    --stage-light: #ffffff;
    --stage-dark: #8e9093;
    --fabric-tan: #d6bf80;
    --fabric-shadow: #2a2418;
    --stitch: #cdb983;
    --ink: #0b0b0b;
    --paper: #ffffff;
  }
  html, body {
    margin: 0;
    padding: 0;
    width: 1200px;
    height: 1000px;
    overflow: hidden;
  }
  .stage {
    position: relative;
    width: 1200px;
    height: 1000px;
    background: radial-gradient(ellipse 55% 75% at 50% 35%, var(--stage-light) 0%, #e6e7e8 45%, var(--stage-dark) 100%);
  }
  .label {
    position: absolute;
    top: 28px;
    width: 472px;
    height: 900px;
    border-radius: 0 0 42px 42px;
    overflow: hidden;
  }
  .label--front { left: 57px; }
  .label--back { left: 672px; }
  .label__fabric {
    position: absolute;
    inset: 0;
    background:
      radial-gradient(ellipse 40% 30% at 40% 50%, rgba(42,36,24,0.45), transparent 70%),
      linear-gradient(160deg, var(--fabric-tan) 0%, #c9b073 40%, #8d7a4c 75%, var(--fabric-shadow) 100%);
  }
  .label__stitch {
    position: absolute;
    inset: 0;
  }
  .brand-name {
    position: absolute;
    margin: 0;
    font-family: "Black Ops One", "Arial Black", sans-serif;
    font-weight: 400;
    font-size: 132px;
    line-height: 1;
    letter-spacing: 4px;
    white-space: nowrap;
    transform-origin: left top;
    transform: rotate(90deg);
  }
  .brand-name--boxed {
    left: 390px;
    top: 135px;
    color: var(--ink);
    background: var(--paper);
    padding: 4px 12px;
  }
  .brand-name--plain {
    left: 463px;
    top: 92px;
    color: var(--ink);
  }
  .size-tag {
    position: absolute;
    left: 84px;
    top: 727px;
    width: 302px;
    height: 107px;
    background: var(--paper);
    color: var(--ink);
    font-family: "Arimo", Arial, sans-serif;
    font-weight: 700;
    font-size: 66px;
    display: flex;
    align-items: center;
    justify-content: center;
    margin: 0;
  }
</style>
</head>
<body>
<main class="stage">
  <section class="label label--front">
    <div class="label__fabric" role="img" aria-label="Close-up photograph of tan chino fabric with a belt loop rivet and folds"></div>
    <svg class="label__stitch" width="472" height="900" viewBox="0 0 472 900" aria-hidden="true">
      <path d="M43 885 V90 Q43 45 88 45 H431 V885 Z" fill="none" stroke="var(--stitch)" stroke-width="7" stroke-dasharray="20 12"/>
    </svg>
    <h1 class="brand-name brand-name--boxed">TARVO</h1>
    <p class="size-tag">32 x 32</p>
  </section>

  <section class="label label--back">
    <div class="label__fabric" role="img" aria-label="Close-up photograph of tan chino fabric with folds"></div>
    <svg class="label__stitch" width="472" height="900" viewBox="0 0 472 900" aria-hidden="true">
      <path d="M43 885 V90 Q43 45 88 45 H431 V885 Z" fill="none" stroke="var(--stitch)" stroke-width="7" stroke-dasharray="20 12"/>
    </svg>
    <h2 class="brand-name brand-name--plain">TARVO</h2>
  </section>
</main>
</body>
</html>
```